Basic business card

use my newly created logo - and the phrases (Leaner Test Budgets & Faster Paths to New Product Launch) - and my new email domain / ID - use at conferences / tradeshows

Industry/Entity Type

semiconductor

Contact Information for Business Card

Daniel K Forde, Owner, communicate via Logo - Lower COT - Cost of Test, Accelerated NPI - New Product Introduction, phone +1 555 613 0946, Larkfield, Nevada, USA, daniel.forde@qal-vub.com

Font styles to use
Sans Serif

Requirements
Nice to have
• re-use my logo created via Pixel Harbor last August (#7315926)

```html
<!DOCTYPE html>
<html lang="en">
<head>
<meta charset="utf-8">
<title>QAL-VUB Business Card</title>
<link rel="stylesheet" href="https://fonts.googleapis.com/css2?family=Montserrat:wght@400;500;700&display=swap">
<style>
  :root {
    --backdrop: #1f2024;
    --card: #4b5874;
    --card-deep: #435069;
    --edge: #3cb6e3;
    --white: #ffffff;
    --green: #7dc22e;
    --cyan: #3cb6e3;
  }
  html, body {
    margin: 0;
    width: 1200px;
    height: 900px;
    overflow: hidden;
    background: var(--backdrop);
    font-family: "Montserrat", sans-serif;
  }
  .canvas {
    position: relative;
    width: 1200px;
    height: 900px;
  }
  .card {
    position: absolute;
    left: 255px;
    width: 690px;
    height: 394px;
    background: var(--card);
    border-radius: 22px;
    border-bottom: 3px solid var(--edge);
    box-sizing: border-box;
    overflow: hidden;
    color: var(--white);
  }
  .card--front { top: 40px; }
  .card--back { top: 466px; }

  .brand {
    position: absolute;
    display: flex;
    align-items: center;
    gap: 14px;
  }
  .brand__mark {
    background: var(--white);
  }
  .brand__name {
    font-weight: 500;
    color: var(--white);
    letter-spacing: 1px;
    white-space: nowrap;
  }
  .card--front .brand { left: 58px; top: 160px; }
  .card--front .brand__mark { width: 34px; height: 34px; }
  .card--front .brand__name { font-size: 44px; }

  .divider {
    position: absolute;
    left: 372px;
    top: 92px;
    width: 2px;
    height: 210px;
    background: var(--green);
  }
  .contact {
    position: absolute;
    left: 398px;
    top: 110px;
  }
  .contact__name {
    margin: 0;
    font-size: 30px;
    font-weight: 700;
    color: var(--green);
    white-space: nowrap;
  }
  .contact__role {
    margin: 2px 0 26px;
    font-size: 17px;
    font-weight: 400;
  }
  .contact__list {
    list-style: none;
    margin: 0;
    padding: 0;
  }
  .contact__item {
    display: flex;
    align-items: center;
    gap: 10px;
    font-size: 17px;
    margin-bottom: 9px;
    white-space: nowrap;
  }
  .contact__icon {
    width: 16px;
    height: 16px;
    flex: none;
    fill: var(--cyan);
  }

  .pattern {
    position: absolute;
    inset: 0;
    background: linear-gradient(135deg, var(--card) 0%, var(--card-deep) 50%, var(--card) 100%);
  }
  .card--back .brand {
    left: 0;
    right: 0;
    top: 120px;
    justify-content: center;
  }
  .card--back .brand__mark { width: 44px; height: 44px; }
  .card--back .brand__name { font-size: 64px; }
  .tagline {
    position: absolute;
    left: 0;
    right: 0;
    top: 230px;
    margin: 0;
    text-align: center;
    font-size: 17px;
    font-weight: 400;
    letter-spacing: 0.5px;
  }
</style>
</head>
<body>
<main class="canvas">

  <section class="card card--front" aria-label="Business card front">
    <div class="brand">
      <span class="brand__mark"></span>
      <span class="brand__name">QAL-VUB</span>
    </div>
    <div class="divider"></div>
    <div class="contact">
      <h1 class="contact__name">Daniel K Forde</h1>
      <p class="contact__role">Owner</p>
      <ul class="contact__list">
        <li class="contact__item">
          <svg class="contact__icon" viewBox="0 0 24 24" aria-hidden="true"><path d="M6.6 10.8a15.1 15.1 0 0 0 6.6 6.6l2.2-2.2a1 1 0 0 1 1-.25 11.4 11.4 0 0 0 3.6.57 1 1 0 0 1 1 1V20a1 1 0 0 1-1 1A17 17 0 0 1 3 4a1 1 0 0 1 1-1h3.5a1 1 0 0 1 1 1c0 1.25.2 2.45.57 3.57a1 1 0 0 1-.25 1z"/></svg>
          +1 555 613 0946
        </li>
        <li class="contact__item">
          <svg class="contact__icon" viewBox="0 0 24 24" aria-hidden="true"><path d="M2 5h20v14H2z M2 5l10 8 10-8" fill="none" stroke="#3cb6e3" stroke-width="2"/></svg>
          daniel.forde@qal-vub.com
        </li>
        <li class="contact__item">
          <svg class="contact__icon" viewBox="0 0 24 24" aria-hidden="true"><path d="M12 2a7 7 0 0 0-7 7c0 5.2 7 13 7 13s7-7.8 7-13a7 7 0 0 0-7-7zm0 9.5A2.5 2.5 0 1 1 12 6.5a2.5 2.5 0 0 1 0 5z"/></svg>
          Larkfield, Nevada, USA
        </li>
      </ul>
    </div>
  </section>

  <section class="card card--back" aria-label="Business card back">
    <div class="pattern" role="img" aria-label="Repeating tone-on-tone brand mark pattern across the card"></div>
    <div class="brand">
      <span class="brand__mark"></span>
      <span class="brand__name">QAL-VUB</span>
    </div>
    <p class="tagline">Leaner Test Budgets &amp; Faster Paths to New Product Launch</p>
  </section>

</main>
</body>
</html>
```